Classy, Elegant, Simple Business Card Design

Looking to have a classy, simple, and elegant design. Want a top notch designed business card. I really like the look of the new torvane credit card. I also like the design I attached. I am trying to reach 21-29 year old females for booking us for there wedding or event. We offer Disc Jockey Service, Photo Booth Rentals, and Uplighting .

Target Market(s)

21-28 year old females

Contact Information for Business Card

Has to have logo, website, email, and phone number

Font styles to use
Other font styles liked:
• open to font choice, modern, clean
Designer to choose
33a6d7
0791cd
0555a3
ffffff

Requirements
Must have
• Has to have logo, website, email, and phone number
Nice to have
• I really like the design of the new torvane credit card. I also included my logo and some designs I like
Should not have
• clutter or too much info

```html
<!DOCTYPE html>
<html lang="en">
<head>
<meta charset="utf-8">
<title>Tidecrest Event Group – Business Card</title>
<link href="https://fonts.googleapis.com/css2?family=Lato:wght@400;700&display=swap" rel="stylesheet">
<style>
  :root {
    --bg: #2b2b2b;
    --card: #ffffff;
    --ink: #222222;
    --blue-light: #33a6d7;
    --blue: #0791cd;
    --blue-deep: #0555a3;
    --rule: #8a8a8a;
    --pattern: #ececec;
  }
  * { margin: 0; padding: 0; box-sizing: border-box; }
  html, body { width: 1200px; height: 1108px; overflow: hidden; }
  body {
    background: var(--bg);
    font-family: "Lato", sans-serif;
    display: flex;
    align-items: center;
    justify-content: center;
    gap: 80px;
  }
  .card {
    width: 420px;
    height: 700px;
    background: var(--card);
    border-radius: 26px;
    position: relative;
    overflow: hidden;
  }
  .card-front {
    display: flex;
    flex-direction: column;
    align-items: center;
    padding-top: 190px;
  }
  .brand-name {
    font-weight: 700;
    font-size: 40px;
    letter-spacing: 2px;
    color: var(--blue-deep);
    display: flex;
    align-items: center;
    gap: 12px;
  }
  .brand-dot {
    width: 16px; height: 16px;
    border-radius: 50%;
    background: var(--blue);
  }
  .brand-tagline {
    margin-top: 8px;
    font-size: 14px;
    letter-spacing: 9px;
    color: #9a9a9a;
    text-transform: uppercase;
  }
  .contact-divider {
    margin-top: 170px;
    width: 300px;
    display: flex;
    align-items: center;
    gap: 8px;
  }
  .contact-divider .line { flex: 1; height: 1px; background: var(--rule); }
  .icon { width: 24px; height: 24px; }
  .contact-list {
    margin-top: 14px;
    list-style: none;
    text-align: center;
    font-size: 19px;
    line-height: 1.35;
    color: var(--ink);
  }
  .services-rule { margin-top: 14px; width: 200px; height: 1px; background: var(--ink); }
  .services {
    margin-top: 12px;
    text-align: center;
    font-size: 19px;
    line-height: 1.3;
    color: var(--ink);
  }
  .card-back .pattern {
    position: absolute; inset: 0;
    background: linear-gradient(160deg, #f6f6f6, var(--pattern));
  }
  .back-mark {
    position: absolute;
    left: 50%; top: 62%;
    transform: translate(-50%, -50%);
    font-weight: 700;
    font-size: 26px;
    letter-spacing: 1px;
    color: var(--blue);
  }
</style>
</head>
<body>
  <section class="card card-front">
    <div class="brand-name"><span class="brand-dot"></span>TIDECREST</div>
    <div class="brand-tagline">Event Group</div>

    <div class="contact-divider">
      <span class="line"></span>
      <svg class="icon" viewBox="0 0 24 24" aria-label="phone"><circle cx="12" cy="12" r="12" fill="var(--blue)"/><path d="M8 6.5c.6-.5 1.4-.4 1.8.2l1 1.6c.3.5.2 1.1-.2 1.5l-.7.6c.6 1.3 1.6 2.3 2.9 2.9l.6-.7c.4-.4 1-.5 1.5-.2l1.6 1c.6.4.7 1.2.2 1.8l-.8.8c-3.5.6-8.8-4.7-8.2-8.2z" fill="#fff"/></svg>
      <svg class="icon" viewBox="0 0 24 24" aria-label="email"><circle cx="12" cy="12" r="12" fill="var(--blue)"/><rect x="6" y="8" width="12" height="8.5" fill="none" stroke="#fff" stroke-width="1.4"/><path d="M6 8l6 5 6-5" fill="none" stroke="#fff" stroke-width="1.4"/></svg>
      <svg class="icon" viewBox="0 0 24 24" aria-label="website"><circle cx="12" cy="12" r="12" fill="var(--blue)"/><circle cx="12" cy="12" r="6" fill="none" stroke="#fff" stroke-width="1.3"/><ellipse cx="12" cy="12" rx="2.5" ry="6" fill="none" stroke="#fff" stroke-width="1.1"/><path d="M6 12h12" stroke="#fff" stroke-width="1.1"/></svg>
      <span class="line"></span>
    </div>

    <ul class="contact-list">
      <li>044-555 010 234</li>
      <li>info@tidecrest.com</li>
      <li>www.tidecrestevents.com</li>
    </ul>
    <div class="services-rule"></div>
    <p class="services">Disc Jockey Service | Uplighting<br>Photo Booth Rentals</p>
  </section>

  <section class="card card-back">
    <div class="pattern" role="img" aria-label="Faint repeating brand monogram pattern"></div>
    <div class="back-mark">TIDECREST</div>
  </section>
</body>
</html>
```